Residential & commercial landscaping company

Updated business cards for commercial and landscaping company. We would like to keep out logo, but just need a more updated business card.

```html
<!DOCTYPE html>
<html lang="en">
<head>
<meta charset="utf-8">
<title>Fernhollow Business Cards</title>
<link href="https://fonts.googleapis.com/css2?family=Arimo:wght@400;700&display=swap" rel="stylesheet">
<style>
  :root {
    --backdrop: #3a3a3a;
    --card-black: #000000;
    --card-white: #ffffff;
    --green: #1e9a3c;
    --green-line: #4cc441;
    --ink: #1a1a1a;
    --grey-text: #3c3c3c;
  }
  html, body {
    margin: 0;
    padding: 0;
    width: 1200px;
    height: 1015px;
    overflow: hidden;
    background: var(--backdrop);
    font-family: "Arimo", Arial, sans-serif;
  }
  .canvas {
    position: relative;
    width: 1200px;
    height: 1015px;
  }
  .card {
    position: absolute;
    left: 320px;
    width: 560px;
    height: 320px;
    box-shadow: 0 10px 30px rgba(0,0,0,0.55);
    overflow: hidden;
  }
  .card-front { top: 150px; background: var(--card-black); }
  .card-back  { top: 545px; background: var(--card-white); }

  .brand {
    position: absolute;
    display: flex;
    align-items: center;
    gap: 14px;
    font-weight: 700;
    letter-spacing: -1px;
  }
  .brand-dot {
    width: 34px;
    height: 34px;
    border-radius: 50%;
    background: var(--green);
    flex: none;
  }
  .card-front .brand {
    left: 0; right: 0; top: 0; bottom: 0;
    justify-content: center;
    font-size: 58px;
    color: #ffffff;
  }
  .card-back .brand {
    right: 46px;
    top: 52px;
    font-size: 44px;
    color: var(--ink);
  }
  .card-back .brand-dot { width: 28px; height: 28px; }

  .divider {
    position: absolute;
    left: 230px;
    right: 30px;
    top: 150px;
    height: 2px;
    background: var(--green-line);
  }
  .person {
    position: absolute;
    left: 36px;
    top: 200px;
  }
  .person-name {
    margin: 0;
    font-size: 26px;
    font-weight: 700;
    color: var(--green);
  }
  .person-title {
    margin: 4px 0 0;
    font-size: 16px;
    color: var(--grey-text);
  }
  .contacts {
    position: absolute;
    left: 240px;
    top: 170px;
    margin: 0;
    padding: 0;
    list-style: none;
    font-size: 16px;
    color: var(--grey-text);
  }
  .contacts li {
    display: flex;
    align-items: center;
    gap: 10px;
    height: 28px;
  }
  .contacts svg { width: 16px; height: 16px; flex: none; fill: var(--green); }
  .contacts .web-name { color: var(--green); }
</style>
</head>
<body>
<main class="canvas">
  <section class="card card-front" aria-label="Business card front">
    <div class="brand"><span class="brand-dot"></span>Fernhollow</div>
  </section>

  <section class="card card-back" aria-label="Business card back">
    <div class="brand"><span class="brand-dot"></span>Fernhollow</div>
    <div class="divider"></div>

    <div class="person">
      <p class="person-name">Daniel Marsh</p>
      <p class="person-title">Jr. Project Manager</p>
    </div>

    <ul class="contacts">
      <li>
        <svg viewBox="0 0 16 16" aria-hidden="true"><path d="M3.5 1.5l2.5 0 1 3.5-1.6 1.2a8 8 0 0 0 4.4 4.4l1.2-1.6 3.5 1 0 2.5c0 .8-.7 1.5-1.5 1.5C6.9 14 2 9.1 2 3c0-.8.7-1.5 1.5-1.5z"/></svg>
        555-201-0148 ext.204
      </li>
      <li>
        <svg viewBox="0 0 16 16" aria-hidden="true"><path d="M4 1h8v4H4zM2 6h12a1 1 0 0 1 1 1v5h-3v3H4v-3H1V7a1 1 0 0 1 1-1zm3 5v3h6v-3z"/></svg>
        555-310-2275
      </li>
      <li>
        <svg viewBox="0 0 16 16" aria-hidden="true"><path d="M1 3h14v10H1zm1.5 1.2V5l5.5 4 5.5-4v-.8L8 8z"/></svg>
        dan@FernhollowLandscape.com
      </li>
      <li>
        <svg viewBox="0 0 16 16" aria-hidden="true"><path d="M8 1a7 7 0 1 0 0 14A7 7 0 0 0 8 1zm0 1.3c.8 0 1.7 1.4 2 3.7H6c.3-2.3 1.2-3.7 2-3.7zM2.4 7h2.5a14 14 0 0 0 0 2H2.4a5.8 5.8 0 0 1 0-2zM6 7h4a12 12 0 0 1 0 2H6a12 12 0 0 1 0-2zm5.1 0h2.5a5.8 5.8 0 0 1 0 2h-2.5a14 14 0 0 0 0-2zM6 10h4c-.3 2.3-1.2 3.7-2 3.7S6.3 12.3 6 10z"/></svg>
        <span>www.<span class="web-name">FernhollowLandscape</span>.com</span>
      </li>
    </ul>
  </section>
</main>
</body>
</html>
```